Sales Page Header Design Project

Hi,
I need a background image created for this sales page: http://trimventurecamp.com
Width: 977 px
Height: 150 px
Here are a few sample designs to work with: http://firmsummitschool.com/
http://craftingamarkweb.com/wp-content/uploads/2011/02/experts1.png
Must be sharp, professional looking and uncluttered.
Colours: Must include blue (I like the blue on the on the current sales page, but will leave shade and colour combinations to your creativity)
Text = Tobi Wanrenu Presents
Trim Venture Camp
Your Blueprint for Building a Profitable, Sustainable Business in Today's Economy!
Any questions, give me a shout
Entrepreneurs and Business Owners, aged 21 to 45
Business

```html
<!DOCTYPE html>
<html lang="en">
<head>
<meta charset="utf-8">
<title>Trim Venture Camp – Sales Page Header</title>
<link rel="stylesheet" href="https://fonts.googleapis.com/css2?family=Arimo:ital,wght@0,400;0,700;1,400&display=swap">
<style>
  :root {
    --page-bg: #f4f4f4;
    --banner-core: #2b7db4;
    --banner-mid: #1a5682;
    --banner-edge: #0a2538;
    --text-white: #ffffff;
    --tagline-cyan: #22d8f2;
  }
  html, body {
    margin: 0;
    padding: 0;
    width: 1200px;
    height: 1000px;
    overflow: hidden;
    background: var(--page-bg);
  }
  .header-banner {
    position: absolute;
    left: 114px;
    top: 373px;
    width: 977px;
    height: 150px;
    background: radial-gradient(ellipse 60% 130% at 50% 70%, var(--banner-core) 0%, var(--banner-mid) 50%, var(--banner-edge) 100%);
    font-family: "Arimo", Helvetica, Arial, sans-serif;
    color: var(--text-white);
    text-align: center;
  }
  .presenter {
    position: absolute;
    top: 16px;
    left: 0;
    width: 100%;
    margin: 0;
    font-size: 15px;
    line-height: 18px;
    letter-spacing: 0.2px;
  }
  .presenter .presents {
    font-size: 9px;
    letter-spacing: 1.2px;
    margin-left: 2px;
  }
  .event-name {
    position: absolute;
    top: 50px;
    left: 0;
    width: 100%;
    margin: 0;
    font-weight: 400;
    font-size: 53px;
    line-height: 56px;
    color: var(--text-white);
  }
  .tagline {
    position: absolute;
    top: 115px;
    left: 0;
    width: 100%;
    margin: 0;
    font-size: 16.5px;
    line-height: 20px;
    font-style: italic;
    color: var(--tagline-cyan);
    letter-spacing: 0.3px;
    text-shadow: 1px 1px 1px rgba(0,0,0,0.7);
  }
</style>
</head>
<body>
  <header class="header-banner">
    <p class="presenter">The Corvel Founders Institute <span class="presents">Presents</span></p>
    <h1 class="event-name">Trim Venture Camp</h1>
    <p class="tagline">Your Blueprint for Building a Profitable, Sustainable Business in Today's Economy!</p>
  </header>
</body>
</html>
```